Build Distinctive Business Card: Public Relations Government Relations firm

I have logo and colors done (attached) need a very cool way to present it on a business card (can be two sided if need be).

Public Relations Government Relations firm

Info:

Paul Marchetti, CEO
Keystone Public Relations
2730 West Harlan Blvd.
Los Angeles CA 90012
(o) 213.555.0148
(f) 213.555.0173
paul@keystonekpr-example.com

Target Market(s)

Government relations, public relations, lobbyist, I was a past State Senator

Industry/Entity Type

Business

Contact Information for Business Card

Info:

Paul Marchetti, CEO
Keystone Public Relations
2730 West Harlan Blvd.
Los Angeles CA 90012
(o) 213.555.0148
(f) 213.555.0173
paul@keystonekpr-example.com
@paulmarchetti

Requirements
Must have
• A sense of balance given logo is already done.
• It's a government relations firm really.
• Lobbyist type.
• Senatorial type...

```html
<!DOCTYPE html>
<html lang="en">
<head>
<meta charset="utf-8">
<title>Keystone Public Relations – Business Card</title>
<link rel="stylesheet" href="https://fonts.googleapis.com/css2?family=Open+Sans:wght@400;600;700&display=swap">
<style>
  :root {
    --bg: #e7e4df;
    --card-white: #ffffff;
    --card-shade: #f1f2f2;
    --brand-blue: #1ba3d6;
    --brand-blue-light: #2ec2e6;
    --brand-blue-deep: #0a7fb4;
    --ink: #1d1d1d;
    --rule: #4a4a4a;
    --paper-text: #ffffff;
  }
  * { box-sizing: border-box; margin: 0; padding: 0; }
  html, body {
    width: 1200px; height: 885px; overflow: hidden;
    background: var(--bg);
    font-family: "Open Sans", Arial, sans-serif;
  }
  .canvas {
    position: relative; width: 1200px; height: 885px;
    display: flex; align-items: center; justify-content: space-between;
    padding: 0 40px;
  }
  .card {
    position: relative; width: 540px; height: 309px;
    border-radius: 3px; overflow: hidden;
    box-shadow: 0 10px 24px rgba(0,0,0,.18);
  }

  /* Front */
  .card-front {
    background: linear-gradient(180deg, var(--card-white) 0%, var(--card-shade) 100%);
  }
  .front-brand {
    position: absolute; left: 34px; top: 92px; width: 200px;
    display: flex; align-items: center; gap: 12px;
  }
  .brand-dot {
    flex: none; width: 62px; height: 62px; border-radius: 50%;
    background: var(--brand-blue);
  }
  .brand-name {
    color: var(--brand-blue); font-weight: 700; line-height: 1.05;
  }
  .brand-name .brand-main { display: block; font-size: 30px; letter-spacing: -0.5px; }
  .brand-name .brand-sub { display: block; font-size: 9px; letter-spacing: 2.2px; text-transform: uppercase; margin-top: 3px; }

  .front-divider {
    position: absolute; left: 262px; top: 42px; width: 1px; height: 172px;
    background: var(--rule);
  }
  .front-contact { position: absolute; left: 288px; top: 50px; right: 18px; }
  .person-name { color: var(--brand-blue); font-size: 27px; font-weight: 400; line-height: 1.1; }
  .person-title { color: var(--ink); font-size: 13px; margin-top: 2px; }
  .contact-list { list-style: none; margin-top: 26px; }
  .contact-list li {
    display: flex; align-items: center; gap: 8px;
    color: var(--ink); font-size: 13.5px; line-height: 1; margin-bottom: 9px;
  }
  .contact-icon { flex: none; width: 16px; height: 16px; }

  .address-band {
    position: absolute; left: 0; right: 0; bottom: 0; height: 66px;
    background: linear-gradient(180deg, var(--brand-blue-light), var(--brand-blue));
    color: var(--paper-text); font-size: 17px;
    display: flex; align-items: center; justify-content: center;
    letter-spacing: 0.2px;
  }

  /* Back */
  .card-back {
    background: radial-gradient(circle at 50% 40%, var(--brand-blue-light) 0%, var(--brand-blue) 45%, var(--brand-blue-deep) 100%);
    display: flex; align-items: center; justify-content: center;
  }
  .back-brand { display: flex; flex-direction: column; align-items: center; gap: 14px; }
  .back-dot { width: 96px; height: 96px; border-radius: 50%; background: var(--paper-text); }
  .back-name { color: var(--paper-text); font-weight: 700; text-align: center; line-height: 1.05; }
  .back-name .brand-main { display: block; font-size: 46px; letter-spacing: -0.5px; }
  .back-name .brand-sub { display: block; font-size: 11px; letter-spacing: 3.4px; text-transform: uppercase; margin-top: 4px; }
</style>
</head>
<body>
<main class="canvas">
  <section class="card card-front" aria-label="Business card front">
    <div class="front-brand">
      <span class="brand-dot" aria-hidden="true"></span>
      <p class="brand-name"><span class="brand-main">Keystone</span><span class="brand-sub">Public Relations</span></p>
    </div>
    <div class="front-divider" aria-hidden="true"></div>
    <div class="front-contact">
      <h1 class="person-name">Paul Marchetti</h1>
      <p class="person-title">CEO</p>
      <ul class="contact-list">
        <li>
          <svg class="contact-icon" viewBox="0 0 16 16" aria-hidden="true"><rect width="16" height="16" fill="#1d1d1d"/><path d="M4 3.5 L6 3.5 L7 6 L5.8 7 Q7 9.5 9 10.2 L10 9 L12.5 10 L12.5 12 Q8 12.5 5.5 9.5 Q3.5 7 4 3.5 Z" fill="#fff"/></svg>
          <span>213.555.0148</span>
        </li>
        <li>
          <svg class="contact-icon" viewBox="0 0 16 16" aria-hidden="true"><rect width="16" height="16" fill="#1d1d1d"/><path d="M4 3.5 L6 3.5 L7 6 L5.8 7 Q7 9.5 9 10.2 L10 9 L12.5 10 L12.5 12 Q8 12.5 5.5 9.5 Q3.5 7 4 3.5 Z" fill="#fff"/></svg>
          <span>213.555.0173</span>
        </li>
        <li>
          <svg class="contact-icon" viewBox="0 0 16 16" aria-hidden="true"><rect width="16" height="16" fill="#1d1d1d"/><rect x="3" y="4.5" width="10" height="7" fill="none" stroke="#fff" stroke-width="1.2"/><path d="M3 4.5 L8 9 L13 4.5 M3 11.5 L6.5 7.8 M13 11.5 L9.5 7.8" fill="none" stroke="#fff" stroke-width="1.2"/></svg>
          <span>paul@keystonekpr-example.com</span>
        </li>
      </ul>
    </div>
    <div class="address-band">2730 West Harlan Blvd. Los Angeles CA 90012</div>
  </section>

  <section class="card card-back" aria-label="Business card back">
    <div class="back-brand">
      <span class="back-dot" aria-hidden="true"></span>
      <p class="back-name"><span class="brand-main">Keystone</span><span class="brand-sub">Public Relations</span></p>
    </div>
  </section>
</main>
</body>
</html>
```